Business Card for a Jewellery Brand

Business card for an upscale jewellery brand. Attached is the brand logo and icon and color board. I am looking for two card versions: one for the founder and one is generic. The card should be elegant and convey upscale and premium feel. I am open to both square and rectangle card shapes.

Industry/Entity Type

Jewelry

Contact Information for Business Card

Two cards: (1) Sunela Parvaniya (Founder) (2) General
(1) Sunela Parvaniya card should have Name: Sunela Parvaniya, Title: Founder Email id: sunela@quiremo.com.au. Phone no: +61452913307
(2) Generic card should have Email id: info@quiremo.com.au. Phone no: +61436207518

Requirements
Must have
• Workmark
• ICON
• Phone no
• Email ID
• ABN: 58219740312 (Note: ABN is Business number in Australia)
• Website: www.quiremo.com.au
• Instagram: quiremo_jewellery
• Facebook: @quiremojewellery
Nice to have
• Tagline

```html
<!DOCTYPE html>
<html lang="en">
<head>
<meta charset="UTF-8">
<title>Quiremo Business Cards</title>
<link href="https://fonts.googleapis.com/css2?family=Jost:wght@400;500&display=swap" rel="stylesheet">
<style>
  :root {
    --backdrop: #2a2a2c;
    --card: #1c1c1d;
    --rose: #e79a93;
    --silver: #cfcfd2;
    --ink-light: #f2f2f2;
  }
  * { margin: 0; padding: 0; box-sizing: border-box; }
  html, body {
    width: 1200px; height: 900px; overflow: hidden;
    background: var(--backdrop);
    font-family: "Jost", "Futura", sans-serif;
  }
  .stage { position: relative; width: 1200px; height: 900px; }
  .card {
    position: absolute; left: 250px;
    width: 700px; height: 400px;
    background: var(--card);
    box-shadow: 0 10px 30px rgba(0,0,0,.45);
  }
  .card--front { top: 40px; }
  .card--back { top: 465px; }

  /* front */
  .front-brand {
    position: absolute; inset: 0;
    display: flex; flex-direction: column; align-items: center; justify-content: center; gap: 26px;
  }
  .front-brand__dot {
    width: 64px; height: 64px; border-radius: 50%;
    border: 3px solid var(--silver);
  }
  .front-brand__name {
    color: var(--silver); font-size: 58px; font-weight: 400; letter-spacing: 20px;
    padding-left: 20px;
  }

  /* back */
  .back-brand {
    position: absolute; left: 40px; top: 0; width: 250px; height: 100%;
    display: flex; align-items: center; justify-content: center;
    color: var(--rose); font-size: 34px; font-weight: 500; letter-spacing: 6px;
  }
  .back-divider {
    position: absolute; left: 310px; top: 90px; width: 3px; height: 240px;
    background: var(--rose);
  }
  .abn {
    position: absolute; right: 44px; top: 42px;
    color: var(--ink-light); font-size: 19px; letter-spacing: 2px;
  }
  .abn__label { color: var(--rose); }
  .person { position: absolute; left: 345px; top: 96px; }
  .person__name { color: var(--rose); font-size: 27px; font-weight: 500; letter-spacing: 2px; text-transform: uppercase; }
  .person__title { color: var(--ink-light); font-size: 19px; font-weight: 500; letter-spacing: 1px; margin-top: 0; }
  .contacts { position: absolute; left: 345px; top: 185px; list-style: none; }
  .contacts li {
    display: flex; align-items: center; gap: 20px; height: 31px;
    color: var(--ink-light); font-size: 21px; letter-spacing: 1.5px;
  }
  .contacts svg { width: 20px; height: 20px; flex: none; }
</style>
</head>
<body>
<main class="stage">
  <section class="card card--front">
    <div class="front-brand">
      <span class="front-brand__dot"></span>
      <span class="front-brand__name">QUIREMO</span>
    </div>
  </section>

  <section class="card card--back">
    <div class="back-brand">QUIREMO</div>
    <div class="back-divider"></div>
    <p class="abn"><span class="abn__label">ABN:</span> 58219740312</p>
    <div class="person">
      <p class="person__name">Sunela Parvaniya</p>
      <p class="person__title">FOUNDER</p>
    </div>
    <ul class="contacts">
      <li>
        <svg viewBox="0 0 20 20"><rect x="5" y="1.5" width="10" height="17" rx="1.5" fill="none" stroke="var(--rose)" stroke-width="2"/></svg>
        +61452913307
      </li>
      <li>
        <svg viewBox="0 0 20 20"><rect x="1.5" y="4" width="17" height="12" fill="var(--rose)"/><path d="M1.5 4 L10 11 L18.5 4" fill="none" stroke="var(--card)" stroke-width="1.6"/></svg>
        www.quiremo.com.au
      </li>
      <li>
        <svg viewBox="0 0 20 20"><circle cx="8" cy="8" r="5.5" fill="none" stroke="var(--rose)" stroke-width="2.2"/><line x1="12" y1="12" x2="18" y2="18" stroke="var(--rose)" stroke-width="2.6" stroke-linecap="round"/></svg>
        sunela@quiremo.com.au
      </li>
      <li>
        <svg viewBox="0 0 20 20"><rect x="2" y="2" width="16" height="16" rx="2" fill="var(--rose)"/></svg>
        quiremo_jewellery
      </li>
      <li>
        <svg viewBox="0 0 20 20"><rect x="2" y="2" width="16" height="16" rx="2" fill="none" stroke="var(--rose)" stroke-width="2"/></svg>
        @quiremojewellery
      </li>
    </ul>
  </section>
</main>
</body>
</html>
```